Business Card Design

I give lessons and clinics for dressage riders
I would like the design to be an outline (with broad lines) of a dressage horse and rider with in background of whole card with print over top tan or parchment card with burgundy print

Industry/Entity Type

Business

Contact Information for Business Card

Dale Ferrin
612-374-2059
Classical dressage training for the modern American
Clinics, lessons, training level -Prix St. George

Requirements
Must have
• broad lined outline of dressage horse and rider

```html
<!DOCTYPE html>
<html lang="en">
<head>
<meta charset="utf-8">
<title>Dale Ferrin – Business Card</title>
<link rel="stylesheet" href="https://fonts.googleapis.com/css2?family=Arimo:wght@400&display=swap">
<style>
  :root {
    --page-bg: #e9e6e1;
    --card-dark: #3b3b3b;
    --card-dark-deep: #2e2e2e;
    --band-grey: #a9a6a8;
    --card-white: #ffffff;
    --art-light: #f1f1f1;
    --art-mid: #c9c9c9;
    --text-main: #ffffff;
    --text-soft: #e4e4e4;
  }
  html, body {
    margin: 0;
    width: 1200px;
    height: 800px;
    overflow: hidden;
    background: var(--page-bg);
  }
  .canvas {
    position: relative;
    width: 1200px;
    height: 800px;
  }
  .card {
    position: absolute;
    left: 75px;
    top: 100px;
    width: 1050px;
    height: 600px;
    overflow: hidden;
    box-shadow: 0 10px 30px rgba(0,0,0,0.18);
    font-family: "Arimo", Arial, sans-serif;
  }
  .card-shapes {
    position: absolute;
    inset: 0;
  }
  .identity {
    position: absolute;
    left: 92px;
    top: 62px;
    color: var(--text-main);
  }
  .identity-name {
    margin: 0;
    font-size: 46px;
    font-weight: 400;
    letter-spacing: 0.5px;
    line-height: 1.1;
  }
  .identity-phone {
    margin: 4px 0 0;
    font-size: 26px;
    color: var(--text-soft);
    letter-spacing: 0.5px;
  }
  .services {
    position: absolute;
    left: 92px;
    top: 282px;
    margin: 0;
    padding: 0;
    list-style: none;
    color: var(--text-soft);
    font-size: 25px;
    line-height: 1.15;
  }
  .services li { margin-bottom: 14px; }
  .services .tagline { width: 470px; margin-bottom: 12px; }
</style>
</head>
<body>
<main class="canvas">
  <section class="card">
    <svg class="card-shapes" width="1050" height="600" viewBox="0 0 1050 600">
      <defs>
        <linearGradient id="darkPanel" x1="0" y1="0" x2="0" y2="1">
          <stop offset="0" stop-color="var(--card-dark-deep)"/>
          <stop offset="1" stop-color="var(--card-dark)"/>
        </linearGradient>
        <linearGradient id="artTone" x1="0" y1="0" x2="1" y2="1">
          <stop offset="0" stop-color="var(--art-light)"/>
          <stop offset="1" stop-color="var(--art-mid)"/>
        </linearGradient>
      </defs>
      <rect class="panel-dark" width="1050" height="600" fill="url(#darkPanel)"/>
      <path class="band-grey" d="M520 0 C600 230 760 460 960 600 L1050 600 L1050 0 Z" fill="var(--band-grey)"/>
      <path class="panel-white" d="M585 0 C660 230 820 470 1020 600 L1050 600 L1050 0 Z" fill="var(--card-white)"/>
      <rect class="horse-rider-art" x="735" y="200" width="280" height="370" rx="8" fill="url(#artTone)" opacity="0.7"
            role="img" aria-label="Broad-lined grey outline of a dressage horse and rider"/>
    </svg>

    <header class="identity">
      <h1 class="identity-name">Dale Ferrin</h1>
      <p class="identity-phone">612-374-2059</p>
    </header>

    <ul class="services">
      <li class="tagline">Classical dressage training for the modern American Clinics</li>
      <li>lessons</li>
      <li>training level</li>
      <li>Prix St. George</li>
    </ul>
  </section>
</main>
</body>
</html>
```